Suds Haven Laundromat Wordpress Design

We need a Wordpress website design for our laundromat, Suds Haven Atlanta, at www.sudshavenatlanta-example.com. We would like to have 6 pages: Home, About Us, Services, Locations, Reviews and Contact us. We will provide content for the text on each page. What we do: We are a full service laundromat that provides dry cleaning drop off, professional laundry services, wash dry fold and self service laundry to the local community. We would like to use the color scheme from our logo to convey a warm, safe, and bright business that caters to its diverse community.
Updates

I like the structure of this laundromat website: http://www.washtroveusa-example.com/ Using my logo and color scheme in the above referenced website is what. Am looking for. The photos attached to the project with the female model should be used as a primary focus and supplemented by actual photos of the equipment.

Target Market(s)

Our target market is a diverse group of people from Midtown Atlanta - LGBTQ community /Locals/Regulars that have been coming to laundromat for 30 years.

Industry/Entity Type

Laundromat

Coding

Coded - Design and coding required

Number of Pages Required

5+ page

Font styles to use
Sans Serif

Colors
0054AA
0677BA
7BADD7
CADEEF
E8F1F8

Requirements
Must have
• Feature this video on the main page: https://videohost-example.com/xq7Rm2bPz4k

```html
<!DOCTYPE html>
<html lang="en">
<head>
<meta charset="utf-8">
<title>Suds Haven Laundromat</title>
<link rel="stylesheet" href="https://fonts.googleapis.com/css2?family=Fredoka:wght@500;600&family=Lexend:wght@300;400;500&family=Yellowtail&display=swap">
<style>
:root{
  --blue-deep:#0054aa;
  --blue:#0677ba;
  --blue-mid:#7badd7;
  --blue-light:#cadeef;
  --blue-pale:#e3eef8;
  --navy:#12205a;
  --gold:#f4b20f;
  --gold-soft:#d9a54a;
  --white:#ffffff;
  --text:#2b3350;
}
*{margin:0;padding:0;box-sizing:border-box}
html,body{width:1200px;height:3495px;overflow:hidden}
body{position:relative;background:var(--white);font-family:"Lexend",sans-serif;color:var(--text)}
.abs{position:absolute}
.script{font-family:"Yellowtail",cursive;color:var(--gold-soft);font-weight:400;white-space:nowrap}
.heading{font-family:"Fredoka",sans-serif;font-weight:600;color:var(--navy)}
.btn{position:absolute;display:flex;align-items:center;justify-content:center;background:var(--gold);color:var(--navy);border-radius:24px;font-weight:500;font-size:16px;width:172px;height:48px}

/* bands */
.band{position:absolute;left:0;width:1200px}
.band-hero{top:0;height:600px;background:var(--blue)}
.band-services{top:1355px;height:405px;background:var(--blue-pale)}
.band-contact{top:2445px;height:520px;background:var(--blue-pale)}
.band-footer{top:2965px;height:530px;background:linear-gradient(180deg,#0a72c0,#0660a8 60%,#0a6ab7)}

/* hero */
.hero-photo{left:580px;top:0;width:620px;height:520px;border-radius:0 0 0 300px;background:linear-gradient(135deg,#d8d4c8,#a9a596 55%,#2e6db4)}
.logo{position:absolute;left:160px;top:46px;color:var(--white);font-family:"Fredoka",sans-serif;font-weight:600;font-size:32px;line-height:1;display:flex;align-items:center;gap:10px}
.logo-dot{width:12px;height:12px;border-radius:50%;background:var(--white)}
.nav{position:absolute;top:17px;left:507px;display:flex;font-size:13px;color:var(--white)}
.nav a{display:block;color:inherit;text-decoration:none;position:relative;margin-right:38px}
.nav a.active{color:var(--gold)}
.nav a.active::after{content:"";position:absolute;left:50%;top:22px;width:5px;height:5px;margin-left:-2px;border-radius:50%;background:var(--gold)}
.hero-voted{left:155px;top:148px;font-size:42px;line-height:48px}
.hero-title{left:160px;top:198px;font-family:"Fredoka",sans-serif;font-weight:600;font-size:58px;line-height:64px;color:var(--white)}
.hero-sub{left:160px;top:332px;font-size:34px;font-style:italic;font-weight:300;color:var(--white)}

/* about */
.about-photo{left:253px;top:738px;width:367px;height:425px;border-radius:8px;background:linear-gradient(160deg,#d9d6cc,#b9b5a8 55%,#3e6fae)}
.about-badge{left:548px;top:1030px;width:118px;height:118px;border-radius:50%;background:var(--gold)}
.about-label{left:672px;top:762px;font-size:34px;line-height:40px}
.about-title{left:675px;top:800px;font-size:50px;line-height:52px}
.about-text{left:676px;top:932px;width:370px;font-size:16.5px;line-height:26.5px;font-weight:300}

/* services */
.services-label{left:0;width:1200px;text-align:center;top:1402px;font-size:34px;line-height:40px}
.services-title{left:0;width:1200px;text-align:center;top:1432px;font-size:48px}
.service{position:absolute;top:1538px;width:205px}
.service-icon{position:absolute;left:-76px;top:0}
.service h3{font-weight:400;font-size:18px;line-height:22px;color:var(--navy)}
.service p{font-size:15px;line-height:23px;font-weight:300;margin-top:4px}
.read{position:absolute;display:flex;align-items:center;gap:6px;font-size:15px;color:var(--navy)}
.read i{display:block;width:16px;height:16px;border-radius:50%;background:var(--gold);color:var(--white);font-style:normal;font-size:14px;line-height:16px;text-align:center}
.read b{display:block;width:36px;height:1px;background:var(--gold);margin-left:-6px}

/* reviews */
.reviews-script{left:446px;top:1952px;font-size:34px;line-height:40px;transform:rotate(-90deg);transform-origin:left top}
.reviews-bar{left:487px;top:1905px;width:2px;height:40px;background:var(--blue-mid)}
.reviews-title{left:504px;top:1850px;font-size:48px;line-height:50px}
.reviews-title span{display:block;font-family:"Lexend",sans-serif;font-weight:300}
.avatar{position:absolute;border-radius:50%}
.quote-badge{left:612px;top:2075px;width:44px;height:44px;border-radius:50%;background:var(--blue);color:var(--white);font-family:"Fredoka",sans-serif;font-weight:600;font-size:22px;text-align:center;line-height:44px}
.reviewer{left:0;width:1200px;text-align:center;top:2126px;font-family:"Fredoka",sans-serif;font-weight:600;font-size:21px;color:var(--navy)}
.reviewer-role{left:0;width:1200px;text-align:center;top:2155px;font-size:15px;font-style:italic;font-weight:300;color:#777}
.stars{left:0;width:1200px;text-align:center;top:2200px;color:var(--gold);font-size:20px;letter-spacing:2px}
.review-text{left:360px;width:480px;top:2232px;text-align:center;font-size:17.5px;line-height:29.5px;font-style:italic;font-weight:300}
.dot{position:absolute;border-radius:50%}

/* contact */
.contact-label{left:158px;top:2530px;font-size:30px;line-height:36px}
.contact-title{left:160px;top:2568px;font-size:40px}
.field{position:absolute;left:158px;width:354px;border-bottom:1px solid #7c8aa2;font-size:15px;font-weight:300;color:var(--navy)}
.map{left:566px;top:2540px;width:475px;height:367px;border-radius:10px;background:linear-gradient(135deg,#eef0f2,#e4e7ea 60%,#cfe5cf)}
.map-tag{left:531px;top:2507px;width:171px;height:132px;border-radius:8px;background:var(--gold);padding:8px}
.map-tag div{width:100%;height:100%;border:1px solid rgba(255,255,255,.7);border-radius:4px;display:flex;align-items:center;justify-content:center;color:var(--white);font-weight:500;font-size:18px}

/* footer */
.footer-center{left:0;width:1200px;text-align:center;color:var(--white)}
.footer-h{font-weight:500;font-size:29px}
.footer-line{font-size:16px}
.social{position:absolute;top:3345px;width:28px;height:28px;border-radius:50%;background:var(--white)}
.copy{left:0;width:1200px;text-align:center;top:3440px;font-size:14px;color:var(--white);font-weight:300}
.copy span{color:var(--gold)}
</style>
</head>
<body>

<!-- HERO -->
<section class="band band-hero">
  <div class="abs hero-photo" role="img" aria-label="Woman in a blue dress seated in front of washing machines"></div>
  <div class="logo"><span class="logo-dot"></span>Suds Haven</div>
  <nav class="nav">
    <a class="active">Home</a><a>About Us</a><a>Services</a><a>Locations</a><a>Reviews</a><a>Contact us</a>
  </nav>
  <div class="abs script hero-voted">Voted</div>
  <div class="abs hero-title">"BEST COIN<br>LAUNDRY"</div>
  <div class="abs hero-sub">Multiple years</div>
  <div class="btn" style="left:160px;top:394px">Know More</div>
</section>

<!-- ABOUT -->
<div class="abs about-photo" role="img" aria-label="Woman in a blue dress pushing a laundry cart past washing machines"></div>
<div class="abs about-badge" role="img" aria-label="Anniversary badge"></div>
<div class="abs script about-label">About</div>
<h2 class="abs heading about-title">Suds Haven<br>Laundromat</h2>
<p class="abs about-text">Lorem ipsum dolor sit amet, consectetur adipiscing elit, sed do eiusmod tempor incididunt ut labore et dolore magna aliqua. Quis ipsum suendisse ultrices gravida. Risus commodo viverra maenas accumsan lacus vel facilisis.</p>
<div class="btn" style="left:676px;top:1093px">Know More</div>

<!-- SERVICES -->
<div class="band band-services"></div>
<div class="abs script services-label">Services</div>
<h2 class="abs heading services-title">Our Special Services</h2>

<div class="service" style="left:234px">
  <svg class="service-icon" width="58" height="54" viewBox="0 0 58 54" aria-hidden="true">
    <rect x="2" y="2" width="48" height="48" rx="4" fill="#e8f1f8" stroke="#12205a" stroke-width="2"/>
    <line x1="2" y1="13" x2="50" y2="13" stroke="#12205a" stroke-width="2"/>
    <circle cx="22" cy="31" r="12" fill="#fff" stroke="#12205a" stroke-width="2"/>
    <rect x="30" y="30" width="26" height="20" rx="3" fill="#f06a6a" stroke="#12205a" stroke-width="2"/>
  </svg>
  <h3>Dry cleaning drop off</h3>
  <p>Lorem ipsum dolor sit amet, consetur adipiscing elit, sed do eiusmod</p>
</div>
<div class="read" style="left:234px;top:1647px">Read More <i>+</i><b></b></div>

<div class="service" style="left:538px">
  <svg class="service-icon" width="56" height="54" viewBox="0 0 56 54" aria-hidden="true">
    <rect x="14" y="2" width="28" height="8" rx="2" fill="#f4b20f" stroke="#12205a" stroke-width="2"/>
    <rect x="10" y="10" width="36" height="10" rx="2" fill="#3a8fd8" stroke="#12205a" stroke-width="2"/>
    <rect x="6" y="20" width="44" height="10" rx="2" fill="#7badd7" stroke="#12205a" stroke-width="2"/>
    <path d="M4 30 H52 L48 52 H8 Z" fill="#f4a13a" stroke="#12205a" stroke-width="2"/>
  </svg>
  <h3>Professional laundry Services</h3>
  <p>Lorem ipsum dolor sit amet, consetur adipiscing</p>
</div>
<div class="read" style="left:538px;top:1647px">Read More <i>+</i><b></b></div>

<div class="service" style="left:843px">
  <svg class="service-icon" width="56" height="54" viewBox="0 0 56 54" aria-hidden="true">
    <line x1="2" y1="6" x2="54" y2="6" stroke="#12205a" stroke-width="2"/>
    <path d="M16 8 L4 18 L10 26 L16 22 V50 H40 V22 L46 26 L52 18 L40 8 C36 14 20 14 16 8 Z" fill="#f06a6a" stroke="#12205a" stroke-width="2"/>
  </svg>
  <h3>Wash dry fold and self service</h3>
  <p>Lorem ipsum dolor sit amet, consetur adiping</p>
</div>
<div class="read" style="left:843px;top:1647px">Read More <i>+</i><b></b></div>

<!-- REVIEWS -->
<div class="abs script reviews-script">Review</div>
<div class="abs reviews-bar"></div>
<h2 class="abs heading reviews-title">Customers<span>Reviews</span></h2>

<div class="avatar" style="left:132px;top:1908px;width:78px;height:78px;background:linear-gradient(#d8c8ba,#b89a86)" role="img" aria-label="Customer portrait"></div>
<div class="avatar" style="left:287px;top:1999px;width:66px;height:66px;background:linear-gradient(#e6dcd4,#a98b78)" role="img" aria-label="Customer portrait"></div>
<div class="avatar" style="left:927px;top:1906px;width:86px;height:86px;background:linear-gradient(#f6e2a8,#c99a6c)" role="img" aria-label="Customer portrait"></div>
<div class="avatar" style="left:889px;top:2076px;width:38px;height:38px;background:linear-gradient(#eee,#b99a8a)" role="img" aria-label="Customer portrait"></div>
<div class="avatar" style="left:162px;top:2244px;width:80px;height:80px;background:linear-gradient(#e9c8b8,#b87e6a)" role="img" aria-label="Customer portrait"></div>
<div class="avatar" style="left:927px;top:2224px;width:80px;height:80px;background:linear-gradient(#e8dfd8,#b97a55)" role="img" aria-label="Customer portrait"></div>
<div class="avatar" style="left:542px;top:1988px;width:116px;height:116px;background:linear-gradient(#efe6e0,#9c6e58);border:4px solid #e4b97a" role="img" aria-label="Portrait of the featured reviewer"></div>
<div class="abs quote-badge">66</div>
<div class="dot" style="left:230px;top:2128px;width:11px;height:11px;background:var(--blue)"></div>
<div class="dot" style="left:842px;top:2002px;width:7px;height:7px;background:var(--gold-soft)"></div>

<div class="abs reviewer">Nora Pellham</div>
<div class="abs reviewer-role">Simply Dummy</div>
<div class="abs stars">★★★★★</div>
<p class="abs review-text">Lorem ipsum dolor sit amet, consectetur adipiscing elit. Cras vel finibus orci, et auctor sem. Fusce vitae est in neque malesuada elementum. Sed placerat ut urna non tempus. Etiam lectus eleifend mattis.</p>

<!-- CONTACT -->
<div class="band band-contact"></div>
<div class="abs script contact-label">Contact Us</div>
<h2 class="abs heading contact-title">Get In Touch</h2>
<div class="field" style="top:2633px;height:31px">Name</div>
<div class="field" style="top:2687px;height:33px">Email</div>
<div class="field" style="top:2745px;height:99px">Your Message</div>
<div class="btn" style="left:163px;top:2866px">Send Now</div>

<div class="abs map" role="img" aria-label="Street map showing the laundromat location"></div>
<div class="abs map-tag"><div>Our Location</div></div>

<!-- FOOTER -->
<div class="band band-footer" role="img" aria-label="Faded photo of washing machines in blue tones"></div>
<div class="abs footer-center footer-h" style="top:3075px">Contact Info</div>
<svg class="abs" style="left:592px;top:3130px" width="16" height="20" viewBox="0 0 16 20" aria-hidden="true">
  <path d="M8 0 C3.6 0 0 3.4 0 7.6 C0 13 8 20 8 20 C8 20 16 13 16 7.6 C16 3.4 12.4 0 8 0 Z" fill="#f4b20f"/><circle cx="8" cy="7.5" r="3" fill="#0a6ab7"/>
</svg>
<div class="abs footer-center footer-line" style="top:3158px">2280 Willowbend Ave NE., # 112</div>
<div class="abs footer-center footer-line" style="top:3188px">Atlanta, GA 30399</div>
<svg class="abs" style="left:591px;top:3216px" width="18" height="18" viewBox="0 0 24 24" aria-hidden="true">
  <path fill="#f4b20f" d="M6.6 10.8c1.4 2.8 3.8 5.1 6.6 6.6l2.2-2.2c.3-.3.7-.4 1-.2 1.1.4 2.3.6 3.6.6.6 0 1 .4 1 1V20c0 .6-.4 1-1 1C10.6 21 3 13.4 3 4c0-.6.4-1 1-1h3.5c.6 0 1 .4 1 1 0 1.3.2 2.5.6 3.6.1.3 0 .7-.2 1L6.6 10.8z"/>
</svg>
<div class="abs footer-center footer-line" style="top:3245px">(404) 555-0148</div>
<div class="abs footer-center" style="top:3303px;font-size:21px">Follow Us</div>
<div class="social" style="left:566px"></div>
<div class="social" style="left:606px"></div>
<div class="abs copy">© 2021 <span>Suds Haven</span>. All right reserved</div>

</body>
</html>
```